Letterhead for Business Law Firm

We need a letter head for our firm based on the design we have settled on and it is attached. Our clients are small and large businesses around the world, and our letterhead is used typically for formal legal purposes such as demand letters (accusing the recipient of doing bad things) or responding to demand letters. It may also be sent to regulators and other government agencies. So this needs to be tasteful, but a little edgy as well - we try to convey that we are a firm that is different - businesses and investors come to us for creative, quick advice, typically in high stress circumstances, and for our ability to work through high conflict situations, and rapid paced engagements.

Target Market(s)

Lawyers, business executives, investors, government regulators who may receive letters from this firm on behalf of its clients.

Industry/Entity Type

Business

Requirements
Must have
• The design and the firm's contact information:
• Thornwell Law Firm, P.C.
• 1876 NE 57th Ave
• Portland, OR 97213
• phone: 971 555 0147
• fax: 971 555 0182
• in what placement and how depicted (e.g. a phone icon instead of the word "phone") I leave to your creative ideas.
Nice to have
• design and information can be placed at the top, bottom and/or sides of the letter, and the design should be for a standard letter size paper - and can have a separate design for the second page.

```html
<!DOCTYPE html>
<html lang="en">
<head>
<meta charset="utf-8">
<title>Thornwell Law Firm, P.C. — Letterhead</title>
<link href="https://fonts.googleapis.com/css2?family=Michroma&family=Source+Sans+3:wght@400&display=swap" rel="stylesheet">
<style>
  :root {
    --paper: #ffffff;
    --ink: #1e1516;
    --teal: #3e6474;
    --teal-deep: #35586a;
    --on-teal: #ffffff;
  }
  * { margin: 0; padding: 0; box-sizing: border-box; }
  html, body { width: 933px; height: 1200px; overflow: hidden; background: var(--paper); }
  .letterhead { position: relative; width: 933px; height: 1200px; background: var(--paper); overflow: hidden; }

  .brand {
    position: absolute; top: 56px; left: 0; width: 100%;
    display: flex; justify-content: center; align-items: center; gap: 14px;
  }
  .brand-mark { width: 22px; height: 22px; background: var(--teal); }
  .brand-name {
    font-family: "Michroma", sans-serif; font-size: 34px; letter-spacing: 6px;
    color: var(--ink); line-height: 1;
  }

  .footer-band {
    position: absolute; left: 0; top: 1020px; width: 933px; height: 180px;
    background: linear-gradient(180deg, var(--teal) 0%, var(--teal-deep) 100%);
  }

  .contact {
    position: absolute; right: 22px; top: 1032px;
    list-style: none; text-align: right;
    font-family: "Source Sans 3", sans-serif; font-size: 18px; color: var(--on-teal);
  }
  .contact li { display: flex; justify-content: flex-end; align-items: center; gap: 6px; height: 27px; line-height: 1; }
  .contact li.address { margin-top: 8px; }
  .contact svg { width: 15px; height: 15px; fill: none; stroke: var(--on-teal); stroke-width: 1.6; flex: none; }
</style>
</head>
<body>
<div class="letterhead">
  <header class="brand">
    <span class="brand-mark"></span>
    <span class="brand-name">THORNWELL</span>
  </header>

  <div class="footer-band" role="img" aria-label="Flowing wave band in dark brown and teal across the foot of the page"></div>

  <ul class="contact">
    <li><svg viewBox="0 0 16 16"><path d="M4 1.5 L6.5 4.5 L5 6.5 C6 8.5 7.5 10 9.5 11 L11.5 9.5 L14.5 12 L12.5 14.5 C7 14 2 9 1.5 3.5 Z"/></svg>971 555 0147</li>
    <li><svg viewBox="0 0 16 16"><rect x="3" y="4" width="10" height="10" rx="1"/><path d="M5 4 V1.5 M5 7 H11 M5 10 H11"/></svg>971 555 0182</li>
    <li><svg viewBox="0 0 16 16"><rect x="1.5" y="4" width="13" height="9"/><path d="M1.5 4 L8 9 L14.5 4"/></svg>info@thornwelllaw.com</li>
    <li><svg viewBox="0 0 16 16"><circle cx="8" cy="8" r="6.5"/><path d="M1.5 8 H14.5 M8 1.5 C5 5 5 11 8 14.5 C11 11 11 5 8 1.5"/></svg>www.thornwelllaw.com</li>
    <li class="address"><svg viewBox="0 0 16 16"><path d="M1.5 14.5 H14.5 M2.5 14.5 V7 L8 3 L13.5 7 V14.5 M5 9 H11 M5 11.5 H11"/></svg>1876 NE 57th Ave, Portland, OR 97213</li>
  </ul>
</div>
</body>
</html>
```